Restaurant Facility Equipment & Store Maintenance/

I need a flyer showing commercial/industrial kitchen equipment photos we work on Hot Equipment & Cold Equipment and offer many services. see attached highlights

```html
<!DOCTYPE html>
<html lang="en">
<head>
<meta charset="utf-8">
<title>Restaurant Facility Equipment Flyer</title>
<link rel="stylesheet" href="https://fonts.googleapis.com/css2?family=Lilita+One&family=Oswald:wght@500;700&family=Poppins:wght@400;500&display=swap">
<style>
  :root {
    --backdrop: #9b9b9b;
    --paper: #ffffff;
    --orange: #f05a22;
    --red: #e8262c;
    --navy: #14142b;
    --blue: #3a64b8;
    --blush: #f9d3c6;
    --ink: #1d1d2b;
  }
  * { margin: 0; padding: 0; box-sizing: border-box; }
  html, body { width: 1200px; height: 2678px; overflow: hidden; background: var(--backdrop); }
  .flyer {
    position: absolute; left: 50px; top: 569px;
    width: 1100px; height: 1540px;
    background: var(--paper); overflow: hidden;
    font-family: "Poppins", sans-serif; color: var(--ink);
  }
  .headline {
    position: absolute; left: 0; top: 30px; width: 100%;
    text-align: center; font-family: "Lilita One", sans-serif;
    font-weight: 400; font-size: 51px; line-height: 59px;
    color: var(--orange);
  }
  .hero { position: absolute; left: 0; top: 280px; width: 1100px; height: 520px; }
  .warranty { position: absolute; left: 758px; top: 636px; width: 280px; height: 280px; }
  .warranty svg { position: absolute; inset: 0; }
  .warranty-text {
    position: absolute; inset: 0; display: flex; flex-direction: column;
    align-items: center; justify-content: center; color: #fff;
    font-family: "Oswald", sans-serif; text-align: center; padding-top: 6px;
  }
  .warranty-days { font-size: 96px; font-weight: 700; line-height: 88px; }
  .warranty-title { font-size: 40px; font-weight: 500; line-height: 44px; }
  .warranty-note { font-size: 27px; font-weight: 500; line-height: 28px; }
  .intro {
    position: absolute; left: 77px; top: 786px; width: 680px;
    font-size: 19px; line-height: 25px;
  }
  .services {
    position: absolute; left: 0; top: 943px; width: 1100px; height: 597px;
    background: var(--navy); border-radius: 40px 40px 0 0;
  }
  .service-list { position: absolute; list-style: none; color: #fff; font-size: 22px; line-height: 28px; }
  .service-list.left { left: 110px; top: 62px; width: 420px; }
  .service-list.right { left: 597px; top: 62px; width: 440px; }
  .service-list li { position: relative; margin-bottom: 10px; }
  .service-list li::before {
    content: ""; position: absolute; left: -29px; top: 12px;
    width: 5px; height: 5px; border-radius: 50%; background: var(--orange);
  }
  .footer-shapes { position: absolute; left: 0; top: 1390px; width: 1100px; height: 150px; }
  .phone {
    position: absolute; left: 47px; top: 1450px; color: #fff;
    font-weight: 500; font-size: 46px; line-height: 60px;
    display: flex; align-items: center; gap: 14px; letter-spacing: 1px;
  }
  .web {
    position: absolute; left: 630px; top: 1466px; height: 32px;
    display: flex; align-items: center; gap: 8px;
    color: #fff; font-size: 27px; font-weight: 500;
  }
</style>
</head>
<body>
<main class="flyer">
  <h1 class="headline">Installation, Rebuilds, OSHA<br>Inspection, and Preventive Maintenance<br>Services for Denver Metro and<br>Surrounding Areas.</h1>

  <svg class="hero" viewBox="0 0 1100 520">
    <defs>
      <linearGradient id="photoTone" x1="0" y1="0" x2="1" y2="1">
        <stop offset="0" stop-color="#5a5a5a"/>
        <stop offset="0.5" stop-color="#b9b9b9"/>
        <stop offset="1" stop-color="#7c7c7c"/>
      </linearGradient>
    </defs>
    <path d="M0 130 C 200 60, 400 30, 600 20 L1100 12 L1100 18 C 700 20, 350 60, 0 170 Z" fill="var(--blush)"/>
    <path role="img" aria-label="Photo of a shopper pushing a cart past shelves of stainless commercial kitchen equipment"
          d="M0 160 C 300 60, 650 20, 1100 16 L1100 374 C 900 450, 650 500, 420 488 C 260 480, 120 445, 0 413 Z"
          fill="url(#photoTone)"/>
  </svg>

  <div class="warranty">
    <svg viewBox="0 0 280 280" width="280" height="280">
      <defs>
        <linearGradient id="badgeTone" x1="0" y1="0" x2="0" y2="1">
          <stop offset="0" stop-color="var(--orange)"/>
          <stop offset="1" stop-color="var(--red)"/>
        </linearGradient>
      </defs>
      <g fill="url(#badgeTone)">
        <circle cx="140" cy="140" r="126"/>
        <circle cx="140" cy="16" r="14"/><circle cx="178" cy="22" r="14"/>
        <circle cx="213" cy="40" r="14"/><circle cx="240" cy="67" r="14"/>
        <circle cx="258" cy="102" r="14"/><circle cx="264" cy="140" r="14"/>
        <circle cx="258" cy="178" r="14"/><circle cx="240" cy="213" r="14"/>
        <circle cx="213" cy="240" r="14"/><circle cx="178" cy="258" r="14"/>
        <circle cx="140" cy="264" r="14"/><circle cx="102" cy="258" r="14"/>
        <circle cx="67" cy="240" r="14"/><circle cx="40" cy="213" r="14"/>
        <circle cx="22" cy="178" r="14"/><circle cx="16" cy="140" r="14"/>
        <circle cx="22" cy="102" r="14"/><circle cx="40" cy="67" r="14"/>
        <circle cx="67" cy="40" r="14"/><circle cx="102" cy="22" r="14"/>
      </g>
    </svg>
    <div class="warranty-text">
      <span class="warranty-days">30</span>
      <span class="warranty-title">DAY WARRANTY</span>
      <span class="warranty-note">On All Oem Parts<br>Installed</span>
    </div>
  </div>

  <p class="intro">We handle everything from the front door to the back door. We offer hot and cold equipment repair, cleaning, maintenance, handyman work, drywall, painting, door closers, floors, and ceiling tiles. For any need in your restaurant, call us and we will send a skilled technician to manage all your commercial and industrial facility requirements.</p>

  <section class="services">
    <ul class="service-list left">
      <li>CFETA Certified Technicians</li>
      <li>Round-the-clock emergency services</li>
      <li>Customers who subscribe to preventive maintenance services receive a reduced rate on hourly labor charges.</li>
      <li>Original equipment manufacturer (OEM) parts</li>
      <li>Equipment Cleaning &amp; Rebuilds</li>
      <li>Used equipment available for purchase or rental</li>
    </ul>
    <ul class="service-list right">
      <li>Installation and Repair of Restaurant Equipment</li>
      <li>Repair or replace restaurant furniture</li>
      <li>Comprehensive licensed electrical contractor services for both interior and exterior projects, including lighting system upgrades.</li>
      <li>Building Graffiti Removal Services</li>
      <li>Hot &amp; Cold Equipment</li>
      <li>Food Service Trucks</li>
      <li>We repair floors, walls, counters, décor, signage, parking lots, dumpsters, and more. If you have it, we probably fix it.</li>
    </ul>
  </section>

  <svg class="footer-shapes" viewBox="0 0 1100 150">
    <defs>
      <linearGradient id="footerTone" x1="0" y1="0" x2="1" y2="0">
        <stop offset="0" stop-color="var(--orange)"/>
        <stop offset="1" stop-color="var(--red)"/>
      </linearGradient>
    </defs>
    <rect x="540" y="76" width="560" height="32" fill="var(--blue)"/>
    <rect x="540" y="108" width="560" height="42" fill="var(--red)"/>
    <path d="M0 10 C 250 0, 460 20, 560 60 C 620 90, 660 130, 760 150 L0 150 Z" fill="url(#footerTone)"/>
  </svg>

  <div class="phone">
    <svg width="40" height="32" viewBox="0 0 40 32" aria-hidden="true">
      <path d="M2 10 C 8 2, 32 2, 38 10 L33 15 L27 11 L27 7 C 22 5, 18 5, 13 7 L13 11 L7 15 Z" fill="#fff"/>
      <path d="M8 17 L14 12 L26 12 L32 17 L32 30 L8 30 Z" fill="#fff"/>
      <circle cx="20" cy="22" r="4" fill="var(--orange)"/>
    </svg>
    <span>045 (7210) 364</span>
  </div>

  <div class="web">
    <svg width="18" height="18" viewBox="0 0 18 18" aria-hidden="true">
      <g fill="none" stroke="#fff" stroke-width="1.4">
        <circle cx="9" cy="9" r="7.5"/><ellipse cx="9" cy="9" rx="3.5" ry="7.5"/>
        <line x1="1.5" y1="9" x2="16.5" y2="9"/>
      </g>
    </svg>
    <span>www.kitchenworksfacility.com</span>
  </div>
</main>
</body>
</html>
```